physio rehab flyer for Vela Mend please

Specification:
Flyer is to be trifold from letter size (8.5 x 11)
-----------------------This may help you:--------------------------
I would like the look of :
clean, minimalistic look with mainly blue and green
san serif font
professional
The colors I like are blue (not the blue in the logo enclosed, I want a change, but more like the blue on my website logo) and light green.
This is my website: www.velamendgroup.ca just so you get an idea but it will be totally changed soon to a to be determined design.
I like the blue and green in file "sample 2" (enclosed)
I like the pictures in "sample 2" file enclosed
For inspiration, I like design of this brochure: http://www.brelford.ca/HarlowRehab/PatientsFamilies/Clinics_Tests/DKAP_Service/Documents/Brochure.pdf
Here's how I see the pages layout:
----[location: this should be the cover (outside, right panel of trifold)]-----
Vela Mend Logo
Integrated Injury Rehab
Evidence-based, one-on-one care to make your recovery fast and comfortable
www.velamendgroup.ca
---------------[location: inside, left panel]----------------------------------------
Our team leaders
[portrait here]
Harriet Olsavik, MD, FRCPC, MSC, CIME
Physiatrist
Dr. Olsavik specializes in injury rehab and sports medicine. She is highly trained having received her MD and Residency in Physiatry from Pellham Institute. Her passion is to help injured people get back to their life.
[portrait here]
Wendy Carstairs, PT
Physiotherapist
Wendy has over 10 years of experience as a Physiotherapist (5 in Canada). She has advanced training in orthopedics and manual therapy. She loves and relates well with people from the youngest to the most senior.
--------------------[location: inside, middle panel]-------------------------------
Our services
We provide integrated assessment and care from interprofessional team of regulated healthcare professionals with proven experience in injury rehabilitation:
physiatrists
sport medicine physicians
physiotherapists
chiropractors
massage therapists
acupuncturists
psychologists
We provide custom medical bracing, orthotics, orthopedic shoes, assistive devices, and medical stockings, all in one place.
----------------------[location: inside, right panel]-----------------------------------
Only registered physiotherapists
We strongly believe in consistency with your treatment plan. This means that you spend your time here one-on-one with your physiotherapist, not any students or assistants. You get consistent high quality care from a professional.
One-on-one attention
We book maximum 3 people per hour to ensure everyone gets adequate one-on-one time with their physiotherapist. This compares favorably with other clinics, who may book upwards of 5-6 per hour. The atmosphere is professional -balanced with friendly, caring and relaxed. Our highly qualified staff operate this way to help make your recovery faster and more enjoyable.
------------------------[location: outside, left panel]---------------------------------
The right rehab for your clients
Timely access to comprehensive assessment and treatment
Proven track record in injury rehabilitation
Convenient one-stop service
Customized treatment plans
Integrated, co-ordinated care
Evidence-based care applying leading best practices
Access to specialty clinics: Physiatry and Chronic Pain
-------------------------[location: outside, middle panel]--------------------------
Please call us 555-384-2096
for more information on injury rehabilitation
Vela Mend Group
1862 Wexmoor Rd., Unit 9
Scarborough, ON K4T 8B2
[Please include a line art map designed based on "map" file enclosed]
To make a referral for your clients, contact velamendgroup@corvamail.ca or fax: 555-384-2071. Thank you.
www.velamendgroup.ca
------------------------------------------------------------------------------------------------
Target Market(s)
family doctors, ER docs, lawyers, and general public age (20-50)
Industry/Entity Type
Health And Wellness
Requirements
Must have
- san serif font
- blue and green colors
- clean, sophisticated look
Nice to have
- consumer choice award badge either on front or back of trifold
- see above

```html
<!DOCTYPE html>
<html lang="en">
<head>
<meta charset="utf-8">
<title>Vela Mend Group – Trifold Flyer</title>
<link rel="stylesheet" href="https://fonts.googleapis.com/css2?family=Exo+2:wght@300;400;500;600;700&display=swap">
<style>
  :root {
    --stage: #5a5a5a;
    --blue: #4a86c8;
    --blue-deep: #3a6fb0;
    --blue-soft: #7eaadc;
    --blue-tab: #5b95d3;
    --green: #8cc63f;
    --green-deep: #76b02e;
    --green-light: #c4e08a;
    --sky-top: #cfe3f5;
    --sky-bottom: #ffffff;
    --ink: #3d4450;
    --white: #ffffff;
    --font: "Exo 2", "Helvetica Neue", Arial, sans-serif;
  }
  * { box-sizing: border-box; margin: 0; padding: 0; }
  html, body { width: 1200px; height: 800px; overflow: hidden; }
  body {
    background: var(--stage);
    font-family: var(--font);
    color: var(--ink);
    position: relative;
  }
  .sheet {
    position: absolute;
    top: 180px;
    width: 570px;
    height: 440px;
    overflow: hidden;
    background: var(--white);
    box-shadow: 0 6px 18px rgba(0,0,0,.35);
  }
  .sheet--outside { left: 20px; }
  .sheet--inside  { left: 610px; background: linear-gradient(180deg, var(--sky-top) 0%, #e9f2fb 45%, var(--sky-bottom) 100%); }

  .panel { position: absolute; top: 0; width: 190px; height: 440px; }
  .panel--left   { left: 0; }
  .panel--middle { left: 190px; }
  .panel--right  { left: 380px; }

  /* ---------- outside ---------- */
  .panel--benefits { background: linear-gradient(180deg, var(--green) 0%, var(--green-deep) 100%); }
  .benefits-photo {
    position: absolute; left: 0; top: 0; width: 190px; height: 190px;
    background: linear-gradient(160deg, #6fae3a 0%, #9ccd5b 55%, #b9dc80 100%);
  }
  .award-badge {
    position: absolute; left: 16px; top: 26px; width: 44px; height: 44px;
    border-radius: 50%; background: #b5252b; border: 3px solid #d9a93a;
  }
  .benefits-title {
    position: absolute; left: 22px; top: 168px; width: 150px;
    background: var(--white); border-radius: 10px;
    padding: 9px 10px; text-align: center;
    color: var(--green-deep); font-weight: 400; font-size: 14px; line-height: 1.1;
  }
  .benefits-list {
    position: absolute; left: 20px; top: 230px; width: 160px;
    list-style: none; color: var(--white); font-size: 8px; font-weight: 400; line-height: 1.3;
  }
  .benefits-list li { position: relative; padding-left: 9px; margin-bottom: 7px; }
  .benefits-list li::before { content: "•"; position: absolute; left: 0; top: 0; }

  .contact-call { position: absolute; left: 18px; top: 28px; width: 160px; color: var(--blue); font-size: 8px; line-height: 1.25; }
  .contact-phone { font-size: 20px; font-weight: 600; color: var(--blue-deep); margin: 2px 0 2px; letter-spacing: .3px; }

  .shapes, .cover-photo { position: absolute; left: 0; top: 0; }

  .contact-address { position: absolute; left: 18px; top: 158px; color: var(--white); font-size: 7.5px; line-height: 1.35; }
  .contact-address strong { font-weight: 600; }
  .map-area {
    position: absolute; left: 18px; top: 200px; width: 155px; height: 95px;
    background: linear-gradient(180deg, #5c93d0 0%, #6a9fd8 100%);
    border: 1px solid rgba(255,255,255,.55);
  }
  .contact-referral { position: absolute; left: 18px; top: 312px; width: 160px; color: var(--white); font-size: 7.5px; line-height: 1.35; }
  .contact-referral strong { font-weight: 600; font-size: 8.5px; }
  .contact-web { position: absolute; left: 18px; top: 400px; color: var(--white); font-size: 8px; }

  .cover-logo {
    position: absolute; left: 396px; top: 108px; width: 78px; height: 78px;
    border-radius: 50%; background: var(--white);
    display: flex; flex-direction: column; align-items: center; justify-content: center;
    color: var(--blue-deep); text-align: center;
    box-shadow: 0 1px 4px rgba(0,0,0,.2);
  }
  .cover-logo-name { font-size: 15px; font-weight: 600; line-height: 1; }
  .cover-logo-sub { font-size: 5.5px; font-weight: 600; margin-top: 3px; }
  .cover-tagline {
    position: absolute; left: 400px; top: 240px; width: 150px;
    color: var(--white); font-size: 13px; font-weight: 300; line-height: 1.2;
  }
  .cover-tagline strong { font-weight: 600; }
  .cover-rule { position: absolute; left: 400px; top: 330px; width: 44px; height: 2px; background: var(--white); }
  .cover-web { position: absolute; left: 400px; top: 400px; color: var(--white); font-size: 8px; }

  /* ---------- inside ---------- */
  .tab {
    display: block; margin: 14px auto 0; width: 150px;
    background: linear-gradient(180deg, var(--blue-soft) 0%, var(--blue-tab) 100%);
    border-radius: 6px; color: var(--white);
    font-size: 11px; font-weight: 400; text-align: center; line-height: 1.15;
    padding: 5px 6px;
  }
  .panel-body { padding: 0 14px; font-size: 7.5px; line-height: 1.38; }
  .portrait {
    width: 62px; height: 62px; border-radius: 50%; margin: 10px auto 4px;
    border: 2px solid var(--white);
    background: linear-gradient(160deg, #a98a74 0%, #d9c2ae 60%, #eee3d6 100%);
  }
  .portrait--second { background: linear-gradient(160deg, #b7b0a8 0%, #d8c6b7 55%, #f1e8df 100%); }
  .leader-name { text-align: center; font-weight: 700; font-size: 8.5px; }
  .leader-role { text-align: center; font-style: italic; font-size: 7px; margin-bottom: 3px; }
  .leader-bio { text-align: justify; }

  .services-intro { margin-top: 12px; }
  .services-list { list-style: none; margin: 6px 0 6px; }
  .services-list li { padding-left: 8px; position: relative; }
  .services-list li::before { content: "•"; position: absolute; left: 0; color: var(--blue); }

  .approach-intro { margin-top: 10px; }
  .tab--inline { margin: 12px auto 8px; width: 140px; }

  .care-photo {
    position: absolute; left: 250px; top: 286px; width: 320px; height: 154px;
    background: linear-gradient(180deg, rgba(238,243,248,0) 0%, #e7d3c4 35%, #c9b3a4 70%, #b59d8c 100%);
  }
</style>
</head>
<body>

<section class="sheet sheet--outside" aria-label="Flyer outside">
  <svg class="shapes" width="570" height="440" viewBox="0 0 570 440" aria-hidden="true">
    <defs>
      <linearGradient id="blueBand" x1="0" y1="0" x2="0" y2="1">
        <stop offset="0" stop-color="#5b95d3"/>
        <stop offset="1" stop-color="#3a6fb0"/>
      </linearGradient>
    </defs>
    <path d="M190,150 C260,128 320,170 400,150 C470,132 520,120 570,96 L570,440 L190,440 Z" fill="url(#blueBand)"/>
  </svg>
  <svg class="cover-photo" width="570" height="440" viewBox="0 0 570 440" role="img" aria-label="Photo of a therapist fitting a knee brace on a patient's leg">
    <defs>
      <linearGradient id="bracePhoto" x1="0" y1="0" x2="1" y2="1">
        <stop offset="0" stop-color="#9fc0e6"/>
        <stop offset=".55" stop-color="#e6d3c6"/>
        <stop offset="1" stop-color="#c9d6e6"/>
      </linearGradient>
    </defs>
    <path d="M380,0 H570 V80 C520,104 470,126 430,132 C410,135 395,142 380,148 Z" fill="url(#bracePhoto)"/>
  </svg>

  <div class="panel panel--left panel--benefits">
    <div class="benefits-photo" role="img" aria-label="Photo of a woman stretching on green grass"></div>
    <div class="award-badge" aria-hidden="true"></div>
    <h2 class="benefits-title">The right rehab for your clients</h2>
    <ul class="benefits-list">
      <li>Timely access to comprehensive assessment and treatment</li>
      <li>Proven track record in injury rehabilitation</li>
      <li>Convenient one-stop service</li>
      <li>Customized treatment plans</li>
      <li>Integrated, co-ordinated care</li>
      <li>Evidence-based care applying leading best practices</li>
      <li>Access to specialty clinics: Physiatry and Chronic Pain</li>
    </ul>
  </div>

  <div class="panel panel--middle">
    <div class="contact-call">
      Please call us
      <div class="contact-phone">555-384-2096</div>
      for more information<br>on injury rehabilitation
    </div>
    <div class="contact-address">
      <strong>Vela Mend Group</strong><br>
      1862 Wexmoor Rd., Unit 9<br>
      Scarborough, ON K4T 8B2
    </div>
    <div class="map-area" role="img" aria-label="Line art map showing the clinic location"></div>
    <p class="contact-referral">
      To make a referral for your clients, contact velamendgroup@corvamail.ca or fax:
      <strong>555-384-2071</strong>. Thank you.
    </p>
    <div class="contact-web">www.velamendgroup.ca</div>
  </div>

  <div class="cover-logo">
    <span class="cover-logo-name">Vela<br>Mend</span>
    <span class="cover-logo-sub">Integrated Injury Rehab</span>
  </div>
  <p class="cover-tagline">Evidence-based, one-on-one care to make <strong>your recovery fast</strong> and <strong>comfortable</strong></p>
  <div class="cover-rule"></div>
  <div class="cover-web">www.velamendgroup.ca</div>
</section>

<section class="sheet sheet--inside" aria-label="Flyer inside">
  <div class="panel panel--left">
    <h2 class="tab">Our team leaders</h2>
    <div class="panel-body">
      <div class="portrait" role="img" aria-label="Portrait of Dr. Harriet Olsavik"></div>
      <p class="leader-name">Harriet Olsavik</p>
      <p class="leader-role">MD, FRCPC, MSC, CIME, Physiatrist</p>
      <p class="leader-bio">Dr. Olsavik specializes in injury rehab and sports medicine. She is highly trained having received her MD and Residency in Physiatry from Pellham Institute. Her passion is to help injured people get back to their life.</p>
      <div class="portrait portrait--second" role="img" aria-label="Portrait of Wendy Carstairs"></div>
      <p class="leader-name">Wendy Carstairs</p>
      <p class="leader-role">PT, Physiotherapist</p>
      <p class="leader-bio">Wendy has over 10 years of experience as a Physiotherapist (5 in Canada). She has advanced training in orthopedics and manual therapy. She loves and relates well with people from the youngest to the most senior.</p>
    </div>
  </div>

  <div class="panel panel--middle">
    <h2 class="tab">Our services</h2>
    <div class="panel-body">
      <p class="services-intro">We provide integrated assessment and care from interprofessional team of regulated healthcare professionals with proven experience in injury rehabilitation:</p>
      <ul class="services-list">
        <li>physiatrists</li>
        <li>sport medicine physicians</li>
        <li>physiotherapists</li>
        <li>chiropractors</li>
        <li>massage therapists</li>
        <li>acupuncturists</li>
        <li>psychologists</li>
      </ul>
      <p>We provide custom medical bracing, orthotics, orthopedic shoes, assistive devices, and medical stockings, all in one place.</p>
    </div>
  </div>

  <div class="panel panel--right">
    <h2 class="tab">Only registered physiotherapists</h2>
    <div class="panel-body">
      <p class="approach-intro">We strongly believe in consistency with your treatment plan. This means that you spend your time here one-on-one with your physiotherapist, not any students or assistants. You get consistent high quality care from a professional.</p>
      <h3 class="tab tab--inline">One-on-one attention</h3>
      <p>We book maximum 3 people per hour to ensure everyone gets adequate one-on-one time with their physiotherapist. This compares favorably with other clinics, who may book upwards of 5-6 per hour. The atmosphere is professional -balanced with friendly, caring and relaxed. Our highly qualified staff operate this way to help make your recovery faster and more enjoyable.</p>
    </div>
  </div>

  <div class="care-photo" role="img" aria-label="Photo of a physiotherapist stretching a patient's leg on a treatment table"></div>
</section>

</body>
</html>
```